High-end construction company needs a business card design

We need a modern looking business card that draws people in, is memorable and looks so good people will want to sick it on their fridges.
On the first side what is needed are:
Logo
My name - Tomasz Brelwik
Title - Managing Director
Website - www.varkelt.co.uk
Email - tomasz@varkelt.co.uk
Telephone - 020 5194 6281
Mobile - 07845139072
On the back side was is needed is a list of all the services we provide:
-Kitchen Renovations
-Bathroom Renovations
-House Renovations
-Garage Conversions
-Extensions
-Loft Conversions
-Conservatories
-Carpentry
-Tiling
-Electrical
-Plumbing & Heating
-Bricklaying
-Landscaping
-Decorating
-Plastering
We would like the colours to be the same shades as on the logo with grey or black for the words.
Target Market(s)
Anyone who needs building work done
Contact Information for Business Card
This business card is for a construction company which strives to deliver excellent service and quality.
The look and feel of the card should represent this.
Requirements
Must have
- On the first side what is needed are:
Logo
My name - Tomasz Brelwik
Title - Managing Director
Website - www.varkelt.co.uk
Email - tomasz@varkelt.co.uk
Telephone - 020 5194 6281
Mobile - 07845139072
Nice to have
- Cool looking features

```html
<!DOCTYPE html>
<html lang="en">
<head>
<meta charset="utf-8">
<title>Varkelt Construction Ltd – Business Card</title>
<link href="https://fonts.googleapis.com/css2?family=Montserrat:wght@400;500;700;800&display=swap" rel="stylesheet">
<style>
  :root {
    --green-deep: #3f8a37;
    --green-mid: #4f9a45;
    --green-light: #7cc04a;
    --green-bright: #8dcf52;
    --white: #ffffff;
    --backdrop: #1e1e1e;
  }
  * { box-sizing: border-box; margin: 0; padding: 0; }
  html, body {
    width: 1200px; height: 930px; overflow: hidden;
    background: var(--backdrop);
    font-family: "Montserrat", Arial, sans-serif;
  }
  .canvas { position: relative; width: 1200px; height: 930px; }
  .card {
    position: absolute; width: 640px; height: 366px;
    border-radius: 22px; overflow: hidden;
    box-shadow: 0 18px 40px rgba(0,0,0,.55);
  }
  /* back side */
  .card-back {
    left: 60px; top: 70px;
    background: linear-gradient(120deg, var(--green-mid) 0%, #5aa44f 45%, var(--green-deep) 100%);
    color: var(--white);
  }
  .services {
    position: absolute; left: 40px; top: 34px;
    list-style: none; font-size: 16.5px; line-height: 19.6px; font-weight: 500;
  }
  .services li { padding-left: 20px; position: relative; }
  .services li::before {
    content: ""; position: absolute; left: 0; top: 6px;
    width: 8px; height: 8px; border-radius: 50%; background: var(--white);
  }
  .brand { position: absolute; text-align: left; font-weight: 800; line-height: 1; }
  .brand-name { display: flex; align-items: center; gap: 10px; font-size: 54px; letter-spacing: 1px; }
  .brand-mark { width: 20px; height: 20px; background: currentColor; }
  .brand-sub { font-size: 17px; letter-spacing: 2.6px; margin-top: 6px; padding-left: 30px; }
  .card-back .brand { left: 330px; top: 120px; color: var(--white); }

  /* front side */
  .card-front { left: 500px; top: 494px; background: var(--white); }
  .card-front .brand { left: 300px; top: 40px; color: var(--green-mid); }
  .wave { position: absolute; left: 0; top: 0; width: 640px; height: 366px; }
  .contact {
    position: absolute; left: 46px; top: 186px; color: var(--white);
    font-size: 14.5px; line-height: 18px; font-weight: 500;
  }
  .contact-name { font-size: 20px; font-weight: 700; line-height: 22px; }
  .contact-title { margin-left: 14px; margin-bottom: 6px; }
  .contact-address { margin-left: 30px; margin-bottom: 4px; }
  .contact-line { display: flex; align-items: center; gap: 7px; margin-left: 30px; }
  .contact-line svg { width: 12px; height: 12px; flex: none; }
</style>
</head>
<body>
<div class="canvas">

  <section class="card card-back" aria-label="Services side">
    <ul class="services">
      <li>Kitchen Renovations</li>
      <li>Bathroom Renovations</li>
      <li>House Renovations</li>
      <li>Garage Conversions</li>
      <li>Extensions</li>
      <li>Loft Conversions</li>
      <li>Conservatories</li>
      <li>Carpentry</li>
      <li>Tiling</li>
      <li>Electrical</li>
      <li>Plumbing &amp; Heating</li>
      <li>Bricklaying</li>
      <li>Landscaping</li>
      <li>Decorating</li>
      <li>Plastering</li>
    </ul>
    <div class="brand">
      <div class="brand-name"><span class="brand-mark"></span>VARKELT</div>
      <div class="brand-sub">CONSTRUCTION LTD</div>
    </div>
  </section>

  <section class="card card-front" aria-label="Contact side">
    <svg class="wave" viewBox="0 0 640 366" preserveAspectRatio="none" aria-hidden="true">
      <defs>
        <linearGradient id="frontGreen" x1="0" y1="0" x2="1" y2="1">
          <stop offset="0" stop-color="#4f9a45"/>
          <stop offset=".5" stop-color="#5ea653"/>
          <stop offset="1" stop-color="#3f8a37"/>
        </linearGradient>
      </defs>
      <path d="M0 168 C150 124 300 200 420 204 C520 207 600 178 640 150 L640 366 L0 366 Z" fill="url(#frontGreen)"/>
      <path d="M0 148 C150 104 300 185 420 188 C520 189 600 160 640 126 L640 140 C600 176 520 199 420 198 C300 196 150 122 0 164 Z" fill="#8dcf52"/>
      <path d="M0 164 C150 122 300 196 420 198 C520 199 600 176 640 140 L640 150 C600 178 520 207 420 204 C300 200 150 124 0 168 Z" fill="#ffffff"/>
    </svg>
    <div class="brand">
      <div class="brand-name"><span class="brand-mark"></span>VARKELT</div>
      <div class="brand-sub">CONSTRUCTION LTD</div>
    </div>
    <div class="contact">
      <div class="contact-name">Tomasz Brelwik</div>
      <div class="contact-title">Managing Director</div>
      <div class="contact-address">14-16 Harrow Lane,<br>London, E2 8QP</div>
      <div class="contact-line">
        <svg viewBox="0 0 16 16"><path fill="#fff" d="M3 1l3 3-2 2c1 2 3 4 5 5l2-2 3 3-2 2C7 14 2 9 1 3z"/></svg>
        020 5194 6281
      </div>
      <div class="contact-line">
        <svg viewBox="0 0 16 16"><rect x="4" y="1" width="8" height="14" rx="1.5" fill="none" stroke="#fff" stroke-width="1.6"/><circle cx="8" cy="12.5" r="1" fill="#fff"/></svg>
        07845139072
      </div>
      <div class="contact-line">
        <svg viewBox="0 0 16 16"><rect x="1" y="3" width="14" height="10" rx="1" fill="none" stroke="#fff" stroke-width="1.6"/><path d="M1 4l7 5 7-5" fill="none" stroke="#fff" stroke-width="1.6"/></svg>
        tomasz@varkelt.co.uk
      </div>
      <div class="contact-line">
        <svg viewBox="0 0 16 16"><circle cx="8" cy="8" r="6.5" fill="none" stroke="#fff" stroke-width="1.4"/><ellipse cx="8" cy="8" rx="3" ry="6.5" fill="none" stroke="#fff" stroke-width="1.2"/><path d="M1.5 8h13" stroke="#fff" stroke-width="1.2"/></svg>
        www.varkelt.co.uk
      </div>
    </div>
  </section>

</div>
</body>
</html>
```